Design NEW business card

We would like a business card using the colour deep red wine or dark navy blue textured background (patterned or not, open to suggestions) with a high gloss debossed rose gold/copper RM Roland Mercer Jewellery business name (Provided). I have included images for your review we would like to keep our currently logo and business name on the front but you can change the layout and positioning. For the back of the card we are open to all suggestions/variations.
Business
Use our current RM Roland Mercer Jewellery logo (Provided image)

```html
<!DOCTYPE html>
<html lang="en">
<head>
<meta charset="utf-8">
<title>Roland Mercer Jewellery – Business Card</title>
<link href="https://fonts.googleapis.com/css2?family=Montserrat:wght@400;600&family=Open+Sans:wght@400;600&display=swap" rel="stylesheet">
<style>
  :root {
    --backdrop: #3a3431;
    --card-navy: #121b2e;
    --card-navy-deep: #0a1020;
    --card-navy-light: #1b2740;
    --card-edge: #070b16;
    --copper: #c08a6a;
    --copper-light: #dcae8f;
    --ink-light: #eef0f4;
    --ink-muted: #9aa1b0;
  }
  * { margin: 0; padding: 0; box-sizing: border-box; }
  html, body { width: 1200px; height: 864px; overflow: hidden; }
  body {
    background: var(--backdrop);
    position: relative;
    font-family: "Open Sans", Arial, sans-serif;
  }
  .card {
    position: absolute;
    width: 540px;
    height: 309px;
    border: 1px solid var(--card-edge);
    box-shadow: 0 14px 30px rgba(0,0,0,.45);
    background-color: var(--card-navy);
    background-image:
      repeating-linear-gradient(45deg, rgba(255,255,255,.018) 0 1px, transparent 1px 4px),
      repeating-linear-gradient(-45deg, rgba(0,0,0,.12) 0 1px, transparent 1px 5px),
      radial-gradient(ellipse at 30% 35%, var(--card-navy-light), var(--card-navy) 55%, var(--card-navy-deep));
  }
  .card--front { left: 60px; top: 90px; }
  .card--back { left: 600px; top: 460px; }

  .brand-name {
    font-family: "Montserrat", Arial, sans-serif;
    font-weight: 400;
    color: var(--copper);
    text-transform: uppercase;
    text-align: center;
    line-height: 1.5;
  }
  .brand-name__main { display: block; font-size: 22px; letter-spacing: 4px; }
  .brand-name__sub { display: block; font-size: 12px; letter-spacing: 9px; }
  .brand-dot {
    display: block;
    width: 10px; height: 10px;
    border-radius: 50%;
    background: var(--copper);
    margin: 0 auto 14px;
  }

  .card--front .brand-name { position: absolute; left: 0; right: 0; top: 100px; }
  .front-web {
    position: absolute; left: 0; right: 0; top: 210px;
    text-align: center;
    font-family: "Montserrat", Arial, sans-serif;
    font-size: 12px;
    letter-spacing: 5px;
    color: var(--ink-muted);
  }

  .card--back .brand-name { position: absolute; left: 20px; width: 270px; top: 108px; }
  .card--back .brand-name__main { font-size: 18px; letter-spacing: 3px; }
  .card--back .brand-name__sub { font-size: 10px; letter-spacing: 7px; }
  .divider {
    position: absolute; left: 300px; top: 40px;
    width: 2px; height: 228px;
    background: linear-gradient(to bottom, transparent, #e8e8e8 50%, transparent);
  }
  .contact { position: absolute; left: 320px; top: 70px; color: var(--ink-light); }
  .contact__name {
    font-weight: 600; font-size: 17px; color: var(--copper-light);
    text-transform: uppercase; letter-spacing: .5px;
  }
  .contact__role { font-size: 13px; color: var(--copper-light); margin-bottom: 6px; }
  .contact__line { font-size: 13px; line-height: 18px; display: flex; align-items: center; gap: 7px; }
  .contact__line svg { width: 11px; height: 11px; fill: var(--copper); flex: none; }
  .contact__address { font-size: 13px; line-height: 18px; padding-left: 18px; }
</style>
</head>
<body>
  <section class="card card--front" aria-label="Card front">
    <div class="brand-name">
      <span class="brand-dot"></span>
      <span class="brand-name__main">Roland Mercer</span>
      <span class="brand-name__sub">Jewellery</span>
    </div>
    <p class="front-web">www.rmjewels.example</p>
  </section>

  <section class="card card--back" aria-label="Card back">
    <div class="brand-name">
      <span class="brand-dot"></span>
      <span class="brand-name__main">Roland Mercer</span>
      <span class="brand-name__sub">Jewellery</span>
    </div>
    <div class="divider"></div>
    <div class="contact">
      <p class="contact__name">Evan Hale</p>
      <p class="contact__role">CEO/FOUNDER</p>
      <p class="contact__address">214 Larkspur Row<br>Juneau, Alaska 99801</p>
      <p class="contact__line"><svg viewBox="0 0 12 12"><path d="M2 1h3l1 3-1.5 1a7 7 0 0 0 2.5 2.5L8 6l3 1v3a1 1 0 0 1-1 1A9 9 0 0 1 1 2a1 1 0 0 1 1-1z"/></svg>907 555 0142</p>
      <p class="contact__line"><svg viewBox="0 0 12 12"><path d="M3 0h6a1 1 0 0 1 1 1v10a1 1 0 0 1-1 1H3a1 1 0 0 1-1-1V1a1 1 0 0 1 1-1zm0 2v7h6V2z"/></svg>907 555 0187</p>
      <p class="contact__line"><svg viewBox="0 0 12 12"><path d="M3 0h5v3H3zM1 4h10v6H1zm2 2v1h2V6z"/></svg>907 555 0119</p>
      <p class="contact__line"><svg viewBox="0 0 12 12"><path d="M0 2h12v1L6 7 0 3zm0 2.5 6 4 6-4V10H0z"/></svg>hello@rmjewels.example</p>
      <p class="contact__line"><svg viewBox="0 0 12 12"><circle cx="6" cy="6" r="5.5"/></svg>www.rmjewels.example</p>
    </div>
  </section>
</body>
</html>
```